Micro Markets Vending business needs a web design

I purchased a logo through MarkHarbor and asked them to design my website but was told they couldn't and that I needed to contact you.
I was building a website through Plume using AI and liked what they had created verbiage-wise but I can't figure out how to finish it the way I would like it. Will send screen shots of what was written, and subsequently used in my slogan under my logo. Would like to use the colors in my logo for my website.
About the company:
RT Snackworks, LLC offers micro market vending machines. Swipe your card, open the doors, take what you want. Can be customized by size for the space, and items for sale within the machines. Pictures of the machines are attached as examples.
I don't need a Testimonials page right now since we are a new company, but will need to add one at some point.
I also like the idea of a contact us button, as shown in the last picture (although it says subscribe). We do not have any emails set up as of yet. Haven't figured out how to do that, but will.
Just let me know what files you need from MarkHarbor for my logo.
Target Market(s)
Apartment complexes, Buildings, Hotels, Gyms, etc
Industry/Entity Type
Vending Machines
Coding
Coded - Design and coding required
Number of Pages Required
1 page
Font styles to use
Other font styles liked:
- Your choice on font style that complements our logo font.
Look and feel
Each slider illustrates characteristics of the customer's brand and the style your logo design should communicate.

```html
<!DOCTYPE html>
<html lang="en">
<head>
<meta charset="utf-8">
<title>RT Snackworks, LLC</title>
<link href="https://fonts.googleapis.com/css2?family=Poppins:wght@300;400;500;600;700;800&family=Roboto:wght@400;500;700&display=swap" rel="stylesheet">
<style>
:root{
  --lime:#a8cc3c;
  --green:#3c9a46;
  --yellow:#e8fb5c;
  --brand:#4a9a2e;
  --ink:#1d1d1d;
  --muted:#555;
  --panel:#f1f1f1;
  --dark:#363636;
  --outline:#9a9a9a;
}
*{box-sizing:border-box;margin:0;padding:0}
html,body{width:1200px;height:3758px;overflow:hidden}
body{font-family:"Poppins",sans-serif;color:var(--ink);background:#fff;position:relative}
section,header,footer{position:relative;width:1200px}
.abs{position:absolute}

/* nav */
.site-nav{height:117px;border-bottom:2px solid var(--yellow)}
.nav-brand{left:95px;top:44px;font-weight:700;font-size:17px;color:var(--brand);display:flex;align-items:center;gap:8px}
.nav-brand i{width:14px;height:14px;background:var(--brand);display:block}
.nav-links{right:104px;top:52px;display:flex;gap:27px;list-style:none;font-size:13.5px;color:#333}
.nav-links .active{color:var(--brand);font-weight:600;border-bottom:2px solid var(--brand);padding-bottom:3px}

/* brand banner */
.brand-banner{height:268px;display:flex;align-items:center;justify-content:center}
.brand-name{font-weight:700;font-size:44px;color:var(--brand);letter-spacing:1px;display:flex;align-items:center;gap:18px}
.brand-name i{width:34px;height:34px;background:var(--brand);display:block}

/* hero */
.hero{height:600px;background:linear-gradient(90deg,#3a3b3c 0%,#2e3236 35%,#27383f 55%,#3f4a3c 80%,#5a4e3a 100%)}
.hero-title{left:107px;top:205px;color:#fff;font-weight:700;font-size:36px;line-height:46px;text-transform:uppercase}
.hero-link{left:105px;top:410px;color:#fff;font-weight:700;font-size:14px;text-decoration:underline;text-underline-offset:4px}

/* section headings */
.eyebrow{font-size:15px;font-weight:500;color:var(--green)}
.outline-title{font-weight:800;font-size:36px;color:transparent;-webkit-text-stroke:1.3px var(--outline);text-shadow:2px 2px 0 #ddd;letter-spacing:.5px;text-transform:uppercase}

/* why */
.why{height:639px;background:var(--panel)}
.why .eyebrow{left:103px;top:87px}
.why .outline-title{left:103px;top:110px}
.cards{left:104px;top:188px;width:992px;height:359px;display:flex}
.card{flex:1;text-align:center;padding:32px 34px 0}
.card.lime{background:var(--lime)}
.card.green{background:var(--green);color:#fff}
.card.yellow{background:var(--yellow)}
.card svg{width:64px;height:84px}
.card h3{font-size:24px;font-weight:600;margin-top:14px}
.card h4{font-size:14px;font-weight:600;margin:6px 0 14px}
.card p{font-size:12px;font-weight:300;line-height:23px}

/* about */
.about{height:583px}
.about-photo{left:127px;top:80px;width:415px;height:403px;background:linear-gradient(135deg,#8a8176,#c9bfb1 50%,#6f7a6a)}
.about-text{left:641px;top:115px;width:445px}
.about-text .outline-title{margin:8px 0 18px}
.about-text p{font-size:14px;font-weight:300;line-height:24px;color:#333;margin-bottom:9px}
.about-text a{display:inline-block;margin-top:6px;font-size:16px;color:#222;text-decoration:underline;text-underline-offset:4px}

/* products */
.products{height:658px}
.products .eyebrow{left:103px;top:26px}
.products .outline-title{left:103px;top:50px}
.view-more{right:104px;top:66px;font-size:16px;font-weight:600;color:#333;text-decoration:underline;text-underline-offset:4px}
.product{top:112px;width:320px}
.product .shot{height:335px}
.product h3{font-family:"Roboto",sans-serif;font-weight:400;font-size:22px;margin-top:32px;color:#222}

/* discover */
.discover{height:361px;background:linear-gradient(180deg,#2b3a52 0%,#3e4c60 55%,#2a2c33 100%);text-align:center;color:#fff}
.discover h2{padding-top:80px;font-size:36px;font-weight:800;color:#e4e4e4;-webkit-text-stroke:1px #8b8b8b;letter-spacing:1px}
.discover p{width:880px;margin:8px auto 0;font-size:15px;line-height:29px}
.discover a{display:inline-block;margin-top:10px;font-size:14px;font-weight:700;color:#fff;text-decoration:underline;text-underline-offset:4px}

/* footer */
.site-footer{height:458px;background:var(--dark);color:#fff}
.subscribe{left:104px;top:50px;font-family:"Roboto",sans-serif}
.subscribe h2{font-size:22px;font-weight:500}
.subscribe p{font-size:13px;margin-top:4px}
.subscribe form{display:flex;gap:6px;margin-top:20px}
.subscribe .field{width:304px;height:54px;background:#fff;color:#333;font-size:13px;padding:19px 14px}
.subscribe .btn{width:120px;height:54px;background:#fff;color:var(--green);font-size:13px;font-weight:700;text-align:center;line-height:54px}
.quick-links{right:104px;top:45px;text-align:right;font-family:"Roboto",sans-serif}
.quick-links h2{font-size:21px;font-weight:500;margin-bottom:8px}
.quick-links li{list-style:none;font-size:15px;line-height:28px}
.quick-links li:first-child{text-decoration:underline}
.footer-brand{left:0;right:0;top:330px;display:flex;justify-content:center}
.footer-brand .brand-name{font-size:38px;color:var(--lime)}
.footer-brand .brand-name i{background:var(--lime);width:30px;height:30px}
.copyright{height:73px;text-align:center;font-size:15px;line-height:73px;color:#333}
</style>
</head>
<body>

<header class="site-nav">
  <div class="nav-brand abs"><i></i>RT Snackworks, LLC</div>
  <ul class="nav-links abs">
    <li class="active">HOME</li><li>WHY CHOOSE US</li><li>PRODUCTS</li><li>TESTIMONIALS</li><li>BLOG</li><li>ABOUT</li>
  </ul>
</header>

<section class="brand-banner">
  <div class="brand-name"><i></i>RT Snackworks, LLC</div>
</section>

<section class="hero" role="img" aria-label="Micro market with lit glass-door drink coolers and snack racks">
  <h1 class="hero-title abs">Your Vending, Your Way<br>Custom Machines For<br>Every Need</h1>
  <a class="hero-link abs">CUSTOMIZE YOURS TODAY!</a>
</section>

<section class="why">
  <p class="eyebrow abs">Our Advantages</p>
  <h2 class="outline-title abs">Why Choose Us</h2>
  <div class="cards abs">
    <div class="card lime">
      <svg viewBox="0 0 64 84" fill="none" stroke="#111" stroke-width="3"><rect x="6" y="4" width="52" height="76" rx="4"/><rect x="13" y="12" width="30" height="42"/><path d="M13 26h30M13 40h30M28 12v42"/><path d="M50 14v34" stroke-dasharray="3 4"/><rect x="16" y="62" width="32" height="8" rx="2"/></svg>
      <h3>Quality Products</h3>
      <h4>Fresh and Varied Selection</h4>
      <p>Our vending machines are stocked with a diverse range of snacks and drinks, ensuring that there's something for everyone. We source only the freshest products for your enjoyment.</p>
    </div>
    <div class="card green">
      <svg viewBox="0 0 64 84" fill="none" stroke="#fff" stroke-width="3"><rect x="14" y="6" width="46" height="72"/><rect x="22" y="14" width="30" height="30"/><path d="M22 29h30M37 14v30"/><circle cx="10" cy="40" r="5"/><path d="M10 46v18l-6 14M10 64l6 14M10 52l12-6"/></svg>
      <h3>Convenience</h3>
      <h4>Easy Access Anytime</h4>
      <p>With RT Snackworks, snack time is just a swipe away. Our machines are strategically located for your convenience, providing quick and easy access to your favorite treats.</p>
    </div>
    <div class="card yellow">
      <svg viewBox="0 0 84 84" fill="none" stroke="#111" stroke-width="3"><path d="M6 20v52h58M6 20c0-8 12-8 12 0v46"/><path d="M18 20h40v16"/><path d="M44 70l26-26v26z"/><path d="M40 52l26-34 6 5-26 34-8 2z"/></svg>
      <h3>Customization</h3>
      <h4>Tailored to Your Tastes</h4>
      <p>Personalize your snacking experience with RT Snackworks. Choose from a wide selection of snacks and drinks to create a vending experience that suits your unique preferences.</p>
    </div>
  </div>
</section>

<section class="about">
  <div class="about-photo abs" role="img" aria-label="Woman selecting an item on a micro market kiosk touchscreen"></div>
  <div class="about-text abs">
    <p class="eyebrow">About Us</p>
    <h2 class="outline-title">RT Snackworks, LLC</h2>
    <p>RT Snackworks, LLC offers micro market vending machines. Swipe your card, open the doors, take what you want. Can be customized by size for the space, and items for sale within the machines. Pictures of the machines are attached as examples.</p>
    <p>With a focus on customer satisfaction, we ensure that our products are always fresh and our machines are well-maintained. Experience the future of vending with RT Snackworks, LLC</p>
    <a>Expolre More</a>
  </div>
</section>

<section class="products">
  <p class="eyebrow abs">RT Snackworks Machines</p>
  <h2 class="outline-title abs">Our Products</h2>
  <a class="view-more abs">View More</a>
  <div class="product abs" style="left:104px">
    <div class="shot" role="img" aria-label="Black snack vending machine stocked with chips" style="background:linear-gradient(160deg,#6d6a63,#2a2a2a 55%,#8a7a52)"></div>
    <h3>Snack Vending Machine</h3>
  </div>
  <div class="product abs" style="left:439px">
    <div class="shot" role="img" aria-label="Navy two-door drink vending cooler" style="background:linear-gradient(160deg,#dcdfe2,#263349 45%,#3a4a5e 75%,#e6e7e8)"></div>
    <h3>Drink Vending Machines</h3>
  </div>
  <div class="product abs" style="left:774px">
    <div class="shot" role="img" aria-label="Self-checkout kiosk beside snack shelves" style="background:linear-gradient(160deg,#5a2a24,#d9d4c8 45%,#3f6fb0 60%,#222)"></div>
    <h3>Coffee Vending Machines</h3>
  </div>
</section>

<section class="discover" role="img" aria-label="City skyline at dusk">
  <h2>DISCOVER OUR RANGE</h2>
  <p>Welcome to RT Snackworks, where convenience meets customization. Our micro market vending machines in Greater Houston, TX, offer a variety of snacks and drinks tailored to your preferences. Swipe your credit card, open the doors, and indulge in what you desire</p>
  <a>CUSTOMIZE YOURS TODAY!</a>
</section>

<footer class="site-footer">
  <div class="subscribe abs">
    <h2>SUBSCRIBE</h2>
    <p>Sign up with your email address to receive news and exclusive prints</p>
    <form><div class="field">Email Address</div><div class="btn">SIGN UP</div></form>
  </div>
  <div class="quick-links abs">
    <h2>QUICK LINKS</h2>
    <ul><li>HOME</li><li>WHY CHOOSE US</li><li>PRODUCTS</li><li>TESTIMONIALS</li><li>BLOG</li><li>ABOUT</li></ul>
  </div>
  <div class="footer-brand abs"><div class="brand-name"><i></i>RT Snackworks, LLC</div></div>
</footer>

<div class="copyright">Copyright © 2024 RT Snackworks , LLC | All rights reserved</div>

</body>
</html>
```